Marlowe Plumbing Heating and Electric

We are looking for a basic, but very beautiful and professional looking website. We would like the ability for a customer to request service through our website via a form or email that will be forwarded to us. Other then that just contact info, our history, our rates, and the services we offer.

Look at his page, it is WAY TOO BASIC, but if gives a very general base line idea: http://www.ringfastpiping.example/

http://www.pipewizard.example/norfolk/

http://www.dranbolt-williamsburg.example/emergency_plumbing.html

Target Market(s)

Heating, air conditioning, plumbing, natural gas

Industry/Entity Type

Plumbing

Number of Pages Required

4 page

Requirements
Must have
• Professional looking, very high end and modern,
Nice to have
• Would like the ability for client to contact us for service through the website utilizing some type of email.

```html
<!DOCTYPE html>
<html lang="en">
<head>
<meta charset="utf-8">
<title>Marlowe Plumbing, Heating, &amp; Electric Inc. — Contact</title>
<link rel="stylesheet" href="https://fonts.googleapis.com/css2?family=Lato:wght@400;700&family=Arimo:ital,wght@0,400;0,700;1,700&display=swap">
<style>
  :root {
    --brand-blue: #29abe2;
    --button-blue: #3a8fe0;
    --nav-active: #2f8de4;
    --heading-dark: #2f2f2f;
    --body-dark: #3a3a3a;
    --emergency-blue: #1a6fb5;
    --alert-red: #e8201f;
    --footer-black: #1c1c1c;
    --panel-white: rgba(255, 255, 255, 0.78);
    --field-border: #cfcfcf;
    --placeholder: #8a8a8a;
    --social-one: #1a6fb8;
    --social-two: #2aa3ef;
    --social-three: #d6382c;
  }
  * { box-sizing: border-box; margin: 0; padding: 0; }
  html, body { width: 1200px; height: 675px; overflow: hidden; }
  body { position: relative; font-family: "Arimo", Arial, sans-serif; background: var(--footer-black); }

  .hero {
    position: absolute; left: 0; top: 0; width: 1200px; height: 600px;
    background:
      radial-gradient(ellipse at 75% 85%, rgba(120, 85, 50, 0.55), transparent 55%),
      radial-gradient(ellipse at 10% 70%, rgba(150, 110, 70, 0.5), transparent 50%),
      linear-gradient(180deg, #b9976a 0%, #e6d2ad 25%, #dcc39b 55%, #a9865c 80%, #6f5538 100%);
  }

  .site-header {
    position: absolute; left: 0; top: 0; width: 1200px; height: 88px;
    background: rgba(60, 50, 40, 0.45);
  }
  .brand {
    position: absolute; left: 246px; top: 28px;
    font-family: "Lato", sans-serif; font-weight: 700; font-size: 24px;
    color: var(--brand-blue); display: flex; align-items: center; gap: 8px;
  }
  .brand-mark { width: 14px; height: 14px; border-radius: 50%; background: var(--brand-blue); }
  .main-nav { position: absolute; top: 14px; right: 252px; display: flex; align-items: center; height: 46px; }
  .main-nav a {
    color: #fff; text-decoration: none; font-size: 12px; font-weight: 700;
    padding: 0 15px; height: 46px; line-height: 46px; display: flex; align-items: center; gap: 5px;
  }
  .main-nav a.is-active { background: var(--nav-active); padding: 0 14px; margin-left: 1px; }

  .company-info { position: absolute; left: 48px; top: 146px; width: 340px; text-align: center; color: var(--body-dark); font-family: "Lato", sans-serif; }
  .company-info h1 { font-size: 24px; font-weight: 700; line-height: 27px; color: var(--heading-dark); }
  .company-info p { font-size: 10.5px; margin-top: 12px; }
  .company-info p + p { margin-top: 11px; }

  .contact-panel {
    position: absolute; left: 414px; top: 131px; width: 364px; height: 395px;
    background: var(--panel-white); border-radius: 3px; padding: 24px 25px 0;
  }
  .contact-panel h2 { text-align: center; color: var(--brand-blue); font-size: 19px; font-weight: 700; height: 29px; margin-top: -1px; }
  .field {
    display: block; width: 314px; height: 28px; margin-bottom: 8px;
    border: 1px solid var(--field-border); background: #fff; border-radius: 2px;
    font: 11px "Arimo", sans-serif; color: var(--placeholder); padding: 0 9px; line-height: 26px;
  }
  .field-message { height: 112px; line-height: 1; padding-top: 9px; }
  .send-button {
    display: block; width: 314px; height: 37px; border: 0; border-radius: 2px;
    background: var(--button-blue); color: #fff; font: 700 11px "Arimo", sans-serif;
  }
  .emergency { text-align: center; margin-top: 10px; font-size: 9px; font-weight: 700; color: var(--emergency-blue); letter-spacing: 0.2px; }
  .emergency-phone { text-align: center; font-size: 28px; font-weight: 700; font-style: italic; color: var(--alert-red); margin-top: 2px; }

  .location-map {
    position: absolute; left: 793px; top: 131px; width: 363px; height: 300px;
    background: linear-gradient(160deg, #eceae4 0%, #e3e1da 60%, #dedbd2 100%);
  }

  .slide-dots { position: absolute; top: 577px; left: 576px; display: flex; gap: 5px; }
  .slide-dots span { width: 10px; height: 10px; border-radius: 50%; background: rgba(255,255,255,0.55); }
  .slide-dots span.is-current { background: #fff; }

  .site-footer { position: absolute; left: 0; top: 600px; width: 1200px; height: 75px; background: var(--footer-black); }
  .copyright { position: absolute; left: 246px; top: 20px; width: 340px; text-align: center; color: #fff; font-size: 11px; line-height: 15px; }
  .social-links { position: absolute; left: 697px; top: 15px; display: flex; gap: 7px; }
  .social-links span { width: 48px; height: 48px; border-radius: 3px; }
  .social-links .s1 { background: var(--social-one); }
  .social-links .s2 { background: var(--social-two); }
  .social-links .s3 { background: var(--social-three); }
</style>
</head>
<body>
  <div class="hero" role="img" aria-label="Photograph of a luxurious cream bathroom with a vanity, columns and a soaking tub"></div>

  <header class="site-header">
    <div class="brand"><span class="brand-mark"></span>Marlowe Plumbing and Heating</div>
    <nav class="main-nav">
      <a href="#">Home</a>
      <a href="#">Services
        <svg width="9" height="6" viewBox="0 0 9 6"><path d="M1 1l3.5 3.5L8 1" fill="none" stroke="#fff" stroke-width="1.8"/></svg>
      </a>
      <a href="#" class="is-active">Contact</a>
    </nav>
  </header>

  <section class="company-info">
    <h1>Marlowe Plumbing, Heating, &amp; Electric Inc.</h1>
    <p>482 Harbor Lane Williamsburg, VA 23185</p>
    <p>Office Hours: 9 am - 5 pm</p>
  </section>

  <form class="contact-panel">
    <h2>Contact Us!</h2>
    <div class="field">Enter your name</div>
    <div class="field">Enter your email address</div>
    <div class="field">Enter your phone number</div>
    <div class="field field-message">Example Text</div>
    <button type="button" class="send-button">SEND</button>
    <p class="emergency">EMERGENCY SERVICE AVAILABLE</p>
    <p class="emergency-phone">757-555-0148</p>
  </form>

  <div class="location-map" role="img" aria-label="Street map showing the office location on Harbor Lane, Williamsburg"></div>

  <div class="slide-dots"><span class="is-current"></span><span></span><span></span></div>

  <footer class="site-footer">
    <p class="copyright">Copyright © Marlowe Plumbing, Heating, &amp; Electrical Inc. | All Rights Reserved</p>
    <div class="social-links">
      <span class="s1" aria-label="Social profile one"></span>
      <span class="s2" aria-label="Social profile two"></span>
      <span class="s3" aria-label="Social profile three"></span>
    </div>
  </footer>
</body>
</html>
```